Wine Lable

We Are Marrowby Estate Wines and we are designing a new bottle for our top end wine named "The Velvet Briar" I no exactly how i want the label to look and im searching for a talented designer to out my vision to life.

There will be 3 parts to this design.

Top Cover design with gold text wrapped around saying"The Velvet Briar" (See Fig 2)

The front label which i want same as attached (See fig 2)

The Rear label
(See Fig 2 for design)
(See Fig 3 for content)

and final bottle design how it will look together
Updates

Come on guys keep the designs coming

Project Deadline Extended
Reason: I have extended my deadline due to the break from work over the Christmas new year period. Extra consideration will be made

Target Market(s)

The High End wine consumers the bottle cost will be $100USD

Font styles to use
Decorative
Script

Requirements
Must have

• Top Cover design with gold text wrapped around saying"The Velvet Briar" (See Fig 2)
Black Rear Label with information and company name (Layout Fig 2) (Content Fig 3)
Gold and Black theme
The Text "Wine of Australia" somewhere on the bottle

```html
<!DOCTYPE html>
<html lang="en">
<head>
<meta charset="utf-8">
<title>Marrowby Estate Wines – The Velvet Briar Label</title>
<link href="https://fonts.googleapis.com/css2?family=Great+Vibes&family=Cinzel:wght@600&family=Libre+Baskerville&display=swap" rel="stylesheet">
<style>
  :root {
    --paper: #ffffff;
    --ink: #0b0b0b;
    --gold: #c9ab1e;
    --gold-light: #f0d76a;
    --gold-deep: #9a7a14;
    --capsule: #1d211f;
    --label-edge: #222222;
  }
  * { margin: 0; padding: 0; box-sizing: border-box; }
  html, body { width: 1200px; height: 1115px; overflow: hidden; background: var(--paper); }
  .canvas { position: relative; width: 1200px; height: 1115px; }

  /* Front label */
  .front-label {
    position: absolute; left: 90px; top: 210px;
    width: 568px; height: 696px;
    background: var(--paper);
    border: 2px solid var(--label-edge);
    border-radius: 3px;
    overflow: hidden;
  }
  .vine-illustration {
    position: absolute; left: 33px; top: 137px;
    width: 450px; height: 290px;
    background: linear-gradient(100deg, #2b2b2b 0%, #5a5a4a 45%, #b8a24a 100%);
    opacity: 0.85;
  }
  .wine-name {
    position: absolute; left: 0; right: 0; top: 462px;
    text-align: center;
    font-family: "Great Vibes", cursive;
    font-weight: 400;
    font-size: 78px; line-height: 1.1;
    color: var(--gold);
    white-space: nowrap;
  }
  .estate-band {
    position: absolute; left: 0; right: 0; bottom: 0; height: 72px;
    background: var(--ink);
    padding: 12px 0 0 78px;
  }
  .estate-band::before, .estate-band::after {
    content: ""; position: absolute; left: 0; right: 0;
    background: linear-gradient(90deg, var(--gold-deep), var(--gold-light), var(--gold), var(--gold-light), var(--gold-deep));
  }
  .estate-band::before { top: 0; height: 3px; }
  .estate-band::after { bottom: 0; height: 5px; }
  .estate-name {
    font-family: "Cinzel", serif; font-weight: 600;
    font-size: 21px; color: var(--paper); letter-spacing: 0.5px;
  }
  .origin {
    font-family: "Libre Baskerville", serif;
    font-size: 15px; color: var(--paper); margin-top: 1px;
  }

  /* Neck capsule */
  .neck-capsule {
    position: absolute; left: 740px; top: 330px;
    width: 380px; height: 230px;
    background: linear-gradient(90deg, #0f1211 0%, var(--capsule) 40%, #2c312e 60%, #0f1211 100%);
    border-radius: 4px;
  }
  .capsule-name {
    position: absolute; left: 0; right: 0; top: 72px;
    text-align: center;
    font-family: "Great Vibes", cursive;
    font-size: 52px; line-height: 1.1;
    color: var(--gold-light);
    white-space: nowrap;
  }
  .capsule-rules { position: absolute; left: 0; top: 150px; width: 380px; height: 20px; }
</style>
</head>
<body>
<main class="canvas">
  <section class="front-label">
    <div class="vine-illustration" role="img" aria-label="Illustration of a black grapevine branch with leaves and a gold grape cluster"></div>
    <h1 class="wine-name">The Velvet Briar</h1>
    <div class="estate-band">
      <p class="estate-name">MARROWBY ESTATE WINES</p>
      <p class="origin">Wine of Australia</p>
    </div>
  </section>

  <section class="neck-capsule">
    <p class="capsule-name">The Velvet Briar</p>
    <svg class="capsule-rules" viewBox="0 0 380 20" aria-hidden="true">
      <line x1="0" y1="3" x2="380" y2="3" stroke="#e2c64a" stroke-width="3"/>
      <line x1="0" y1="14" x2="380" y2="14" stroke="#e2c64a" stroke-width="3"/>
    </svg>
  </section>
</main>
</body>
</html>
```